Custom unique Stationary design for Logistics company

We need a custom, unique , elegant and luxurious full stationary design using our new logo, following these guidelines:
1- Business card: double sided, both sides uses the navy blue as the background main color (same as the code of the navy blue used in our logo).
2- envelope and folder: also use the same navy blue as the main background color.
3- book cover( notepad cover) : same thing with the navy blue
4- letterhead: feel free to use the combination of the colors in our logo.
5- rest of the items are up to your creativity

Target Market(s)

corporates and other businesses

Industry/Entity Type

Logistics and heavy machines contractors

Requirements
Must have
• Letterhead, business card, envelope, notepad cover, paper, file
Nice to have
• navy blue to be main background color for business card, envelope, notepad cover

```html
<!DOCTYPE html>
<html lang="en">
<head>
<meta charset="utf-8">
<title>Meridian Haulage Group — Stationery</title>
<link href="https://fonts.googleapis.com/css2?family=Montserrat:wght@400;600;700&family=Open+Sans:wght@400;600&display=swap" rel="stylesheet">
<style>
  :root{
    --navy:#1f5679;
    --navy-deep:#184764;
    --orange:#e2622c;
    --paper:#ffffff;
    --stage:#e3e4e5;
    --stage-alt:#d9dadb;
    --ink:#3b3f44;
    --muted:#8a8f95;
    --rule:#ffffff;
  }
  *{box-sizing:border-box;margin:0;padding:0}
  html,body{width:1200px;height:5396px;overflow:hidden}
  body{position:relative;background:var(--rule);font-family:"Open Sans",Arial,sans-serif;color:var(--ink)}
  .section{position:absolute;left:0;width:1200px;background:var(--stage)}
  .sec-cards{top:0;height:944px;background:linear-gradient(#d4d5d6,#eceded)}
  .sec-letter{top:952px;height:1264px;background:linear-gradient(#d6d7d8,#ececec)}
  .sec-envelopes{top:2224px;height:1372px;background:#e6e7e8}
  .sec-folder{top:3604px;height:912px;background:linear-gradient(#eaebec,#d7d8d9)}
  .sec-notebook{top:4524px;height:872px;background:linear-gradient(#eceded,#d9dadb)}
  .sheet{position:absolute;background:var(--paper);box-shadow:0 6px 18px rgba(0,0,0,.16)}
  .navy{background:var(--navy)}

  .brand{display:inline-flex;align-items:center;gap:10px;font-family:"Montserrat",Arial,sans-serif;font-weight:700;color:var(--navy);letter-spacing:.5px;white-space:nowrap}
  .brand .dot{display:inline-block;border-radius:50%;background:var(--orange)}
  .brand.on-navy{color:#fff}
  .brand.lg{font-size:30px}.brand.lg .dot{width:16px;height:16px}
  .brand.md{font-size:20px}.brand.md .dot{width:11px;height:11px}
  .brand.sm{font-size:13px;gap:6px}.brand.sm .dot{width:7px;height:7px}
  .brand.xs{font-size:10px;gap:5px}.brand.xs .dot{width:6px;height:6px}
  .center{position:absolute;left:50%;top:50%;transform:translate(-50%,-50%)}

  /* business cards */
  .card{width:440px;height:252px}
  .card-front{left:150px;top:300px}
  .card-back{left:610px;top:300px;padding:26px 28px}
  .card-back .brand{position:absolute;right:28px;top:26px}
  .card-back .stripe{position:absolute;left:0;top:96px;width:100%;height:4px;background:var(--navy)}
  .card-back .person{position:absolute;left:28px;top:120px}
  .person-name{font-family:"Montserrat",Arial,sans-serif;font-weight:700;font-size:15px;color:var(--navy);letter-spacing:1px}
  .person-role{font-size:10px;color:var(--orange);font-weight:600;margin-top:2px}
  .contact-list{list-style:none;margin-top:14px;font-size:10px;line-height:17px}
  .contact-list li{display:flex;align-items:center;gap:7px}
  .contact-list svg{width:11px;height:11px}
  .card-back .address{position:absolute;right:28px;top:120px;text-align:right;font-size:10px;line-height:15px}
  .card-back .address strong{font-weight:600;color:var(--navy)}

  /* letterhead */
  .letterhead{left:320px;top:130px;width:560px;height:792px;padding:54px 48px}
  .letterhead .head{text-align:center}
  .letter-body{margin-top:44px;font-size:9.5px;line-height:15px;color:#555}
  .letter-body p{margin-bottom:12px}
  .signature{width:44px;height:36px;background:#e7e9ec;border-radius:3px;margin:6px 0 12px}
  .letter-foot{position:absolute;left:48px;right:48px;bottom:44px;display:flex;justify-content:space-between;font-size:9px;line-height:14px}
  .letter-foot .address{text-align:right}
  .letter-foot .contact-list{margin:0;font-size:9px;line-height:14px}

  /* envelopes */
  .env-front .brand{position:absolute;left:22px;top:24px}
  .env-front .return{position:absolute;left:22px;top:50px;font-size:7.5px;line-height:11px;color:var(--muted)}
  .env-window{position:absolute;border:1.5px solid #c9ccd0;border-radius:6px;background:#f7f8f9}
  .env-back{overflow:hidden}
  .env-back .flap{position:absolute;left:0;top:0;width:100%;background:var(--navy)}
  .env-back .flap svg{position:absolute;left:0;bottom:-1px;width:100%}
  .env-a{width:420px;height:560px}
  .env-b{width:420px;height:300px}
  .env-c{width:420px;height:200px}

  /* folder */
  .folder{left:160px;top:150px;width:880px;height:600px;display:flex;box-shadow:0 10px 28px rgba(0,0,0,.2)}
  .folder .panel{position:relative;width:50%;height:100%}
  .folder .inside{background:var(--paper)}
  .folder .url{position:absolute;right:40px;bottom:40px;font-size:10px;color:var(--navy);letter-spacing:.5px}

  /* notebook */
  .notepad-open{left:150px;top:210px;width:500px;height:360px;display:flex;background:none;box-shadow:none}
  .notepad-open .page{position:relative;width:50%;height:100%;background:#fbfbfb;box-shadow:0 6px 18px rgba(0,0,0,.14)}
  .notepad-open .page + .page{border-left:1px solid #e2e2e2}
  .notepad-open .brand{position:absolute;left:24px;top:24px}
  .notebook-cover{left:730px;top:130px;width:320px;height:440px;border-radius:4px 10px 10px 4px}
  .notebook-cover .band{position:absolute;right:34px;top:0;width:8px;height:100%;background:var(--navy-deep)}
</style>
</head>
<body>

<!-- Business cards -->
<section class="section sec-cards">
  <div class="sheet card card-front navy">
    <span class="brand lg on-navy center"><span class="dot"></span>Meridian Haulage</span>
  </div>
  <div class="sheet card card-back">
    <span class="brand sm"><span class="dot"></span>Meridian Haulage</span>
    <div class="stripe"></div>
    <div class="person">
      <div class="person-name">MARCUS ELLERY</div>
      <div class="person-role">Operations Director</div>
      <ul class="contact-list">
        <li><svg viewBox="0 0 12 12"><circle cx="6" cy="6" r="6" fill="#e2622c"/><path d="M4 3.2l1 1.6-.6.6a4 4 0 002 2l.6-.6 1.6 1-.6 1.1C6 9 3 6 2.9 3.9z" fill="#fff"/></svg>555-014-2276</li>
        <li><svg viewBox="0 0 12 12"><circle cx="6" cy="6" r="6" fill="#e2622c"/><rect x="3" y="4" width="6" height="4.2" fill="#fff"/><path d="M3 4l3 2.2L9 4" stroke="#e2622c" stroke-width=".7" fill="none"/></svg>info@meridianhaul.com</li>
        <li><svg viewBox="0 0 12 12"><circle cx="6" cy="6" r="6" fill="#e2622c"/><circle cx="6" cy="6" r="3" fill="none" stroke="#fff" stroke-width=".8"/><path d="M3 6h6M6 3v6" stroke="#fff" stroke-width=".7"/></svg>www.meridianhaul.com</li>
      </ul>
    </div>
    <div class="address"><strong>Meridian Haulage Group</strong><br>48 Harbor Crest Road<br>Oakvale, ON K2P 4R7</div>
  </div>
</section>

<!-- Letterhead -->
<section class="section sec-letter">
  <div class="sheet letterhead">
    <div class="head"><span class="brand md"><span class="dot"></span>Meridian Haulage</span></div>
    <div class="letter-body">
      <p>Dear customer,</p>
      <p>We are pleased to confirm the schedule for your upcoming heavy equipment transfer. Our dispatch team has reviewed the route, permits and escort needs, and all units will be loaded at your yard on the agreed date.</p>
      <p>Each machine is secured, inspected and tracked from pickup to delivery. You will receive status updates at every stage, along with signed condition reports once the load arrives safely on site.</p>
      <p>Please contact our office with any questions. We value your trust and look forward to a smooth and timely project.</p>
      <p>Yours sincerely,</p>
      <div class="signature" role="img" aria-label="Handwritten signature"></div>
    </div>
    <div class="letter-foot">
      <ul class="contact-list">
        <li><svg viewBox="0 0 12 12"><circle cx="6" cy="6" r="6" fill="#e2622c"/></svg>555-014-2276</li>
        <li><svg viewBox="0 0 12 12"><circle cx="6" cy="6" r="6" fill="#e2622c"/></svg>info@meridianhaul.com</li>
        <li><svg viewBox="0 0 12 12"><circle cx="6" cy="6" r="6" fill="#e2622c"/></svg>www.meridianhaul.com</li>
      </ul>
      <div class="address">Meridian Haulage Group<br>48 Harbor Crest Road<br>Oakvale, ON K2P 4R7</div>
    </div>
  </div>
</section>

<!-- Envelopes -->
<section class="section sec-envelopes">
  <div class="sheet env-front env-a" style="left:160px;top:96px">
    <span class="brand sm"><span class="dot"></span>Meridian Haulage</span>
    <div class="return">48 Harbor Crest Road<br>Oakvale, ON K2P 4R7</div>
    <div class="env-window" style="left:24px;top:130px;width:170px;height:70px"></div>
  </div>
  <div class="sheet env-back env-a" style="left:620px;top:96px">
    <div class="flap" style="height:90px">
      <span class="brand xs on-navy center" style="top:40%"><span class="dot"></span>Meridian Haulage</span>
    </div>
  </div>

  <div class="sheet env-front env-b" style="left:160px;top:700px">
    <span class="brand sm"><span class="dot"></span>Meridian Haulage</span>
    <div class="return">48 Harbor Crest Road<br>Oakvale, ON K2P 4R7</div>
    <div class="env-window" style="left:24px;top:140px;width:170px;height:60px"></div>
  </div>
  <div class="sheet env-back env-b" style="left:620px;top:700px">
    <div class="flap" style="height:76px">
      <span class="brand xs on-navy center" style="top:40%"><span class="dot"></span>Meridian Haulage</span>
    </div>
  </div>

  <div class="sheet env-front env-c" style="left:160px;top:1070px">
    <span class="brand sm"><span class="dot"></span>Meridian Haulage</span>
    <div class="return">48 Harbor Crest Road<br>Oakvale, ON K2P 4R7</div>
    <div class="env-window" style="left:24px;top:100px;width:150px;height:52px"></div>
  </div>
  <div class="sheet env-back env-c" style="left:620px;top:1070px">
    <div class="flap" style="height:64px">
      <span class="brand xs on-navy center" style="top:40%"><span class="dot"></span>Meridian Haulage</span>
    </div>
  </div>
</section>

<!-- Presentation folder -->
<section class="section sec-folder">
  <div class="sheet folder">
    <div class="panel navy"></div>
    <div class="panel inside">
      <span class="brand lg center"><span class="dot"></span>Meridian Haulage</span>
      <div class="url">www.meridianhaul.com</div>
    </div>
  </div>
</section>

<!-- Notepad -->
<section class="section sec-notebook">
  <div class="sheet notepad-open">
    <div class="page"><span class="brand xs"><span class="dot"></span>Meridian Haulage</span></div>
    <div class="page"></div>
  </div>
  <div class="sheet notebook-cover navy">
    <span class="brand md on-navy center"><span class="dot"></span>Meridian Haulage</span>
    <div class="band"></div>
  </div>
</section>

</body>
</html>
```